Quorva - corporate Business Card

We need a good look and innovative business card for a new start up company based in Los Angeles called "Quorva". We are in a payment business, including payment card, app, and ewallet. We are expert in online payment and Card not present (CNP) transaction.
We need an innovative, modern business card.

Our logo font is Aero Matics

Target Market(s)

Startup - Bank - Online Payment - Card Manufacturing

Industry/Entity Type

Startup

Contact Information for Business Card

phone: 555 014 7396 - Address: 4172 Marlowe blvd, Ashbury Heights, OR 97390

Requirements
Must have
• Message: innovative, professional, expert, high tech, trust, online payment expert, security
Nice to have
• no comment
Should not have
• no Comment

```html
<!DOCTYPE html>
<html lang="en">
<head>
<meta charset="utf-8">
<title>Quorva – Business Card</title>
<link rel="stylesheet" href="https://fonts.googleapis.com/css2?family=Exo+2:wght@400;500;600;700&display=swap">
<style>
  :root {
    --brand-red: #a81b2b;
    --card-white: #ffffff;
    --ink: #2a2a2a;
    --ink-soft: #444444;
    --backdrop: #e9e6e1;
  }
  * { margin: 0; padding: 0; box-sizing: border-box; }
  html, body {
    width: 1200px;
    height: 736px;
    overflow: hidden;
    background: var(--backdrop);
    font-family: "Exo 2", sans-serif;
  }
  .stage {
    position: relative;
    width: 1200px;
    height: 736px;
  }
  .card {
    position: absolute;
    top: 219px;
    width: 520px;
    height: 298px;
    border-radius: 16px;
    box-shadow: 0 6px 18px rgba(0,0,0,0.12);
  }

  /* Front */
  .card-front {
    left: 50px;
    background: var(--brand-red);
    color: var(--card-white);
  }
  .brand-lockup {
    position: absolute;
    left: 130px;
    top: 106px;
    display: flex;
    align-items: center;
    gap: 12px;
  }
  .brand-dot {
    width: 58px;
    height: 58px;
    border-radius: 50%;
    background: var(--card-white);
  }
  .brand-name {
    font-size: 46px;
    font-weight: 600;
    letter-spacing: 0.5px;
    line-height: 1;
    color: var(--card-white);
  }
  .tagline {
    position: absolute;
    left: 30px;
    bottom: 26px;
    font-size: 9.5px;
    letter-spacing: 0.6px;
    color: var(--card-white);
    white-space: nowrap;
  }

  /* Back */
  .card-back {
    left: 630px;
    background: var(--card-white);
    color: var(--ink);
  }
  .holder {
    position: absolute;
    right: 46px;
    top: 34px;
    text-align: left;
  }
  .holder-name {
    font-size: 19px;
    font-weight: 600;
    letter-spacing: 1px;
    text-transform: uppercase;
    line-height: 1.1;
  }
  .holder-role {
    font-size: 11px;
    font-weight: 600;
    color: var(--ink-soft);
  }
  .back-dot {
    position: absolute;
    right: 46px;
    top: 156px;
    width: 28px;
    height: 28px;
    border-radius: 50%;
    background: var(--brand-red);
  }
  .contact {
    position: absolute;
    left: 40px;
    bottom: 40px;
    padding-left: 14px;
    border-left: 4px solid var(--brand-red);
    list-style: none;
    font-size: 11.5px;
    font-weight: 500;
    line-height: 1.45;
    color: var(--ink);
    white-space: nowrap;
  }
</style>
</head>
<body>
  <main class="stage">
    <section class="card card-front" aria-label="Business card front">
      <div class="brand-lockup">
        <span class="brand-dot" aria-hidden="true"></span>
        <span class="brand-name">quorva</span>
      </div>
      <p class="tagline">innovative • professional • expert • high tech • trust • online payment expert • security</p>
    </section>

    <section class="card card-back" aria-label="Business card back">
      <div class="holder">
        <p class="holder-name">Daniel Reyes</p>
        <p class="holder-role">President</p>
      </div>
      <span class="back-dot" aria-hidden="true"></span>
      <ul class="contact">
        <li>555 014 7396</li>
        <li>daniel@quorvapay.com</li>
        <li>www.quorvapay.com</li>
        <li>4172 Marlowe blvd, Ashbury Heights, OR 97390</li>
      </ul>
    </section>
  </main>
</body>
</html>
```